Lumra Learning Web Design Project

Who We are:
Lumra Learning is education information portal/ magazine, providing information about the Chinese and International education markets. Our aim is to help school principals improve there curriculum, and parents in understanding this curriculum.

Project Brief:
The site will include education news updates, educational services, curriculum developments and overseas study. We hope the site represents the cross cultural bridge between the west and east. The site will cover both the Sciences and Arts.

Note:
The logo design competition is also underway so we only need the website design

What We want:
This competition is for Design only no coding!
Design a home page based on Template 1,2 or 3. I only need to select one.
The design of an article page.

Optional
Design a Parvex Shutters metro style splash page.

Sites We like:
http://www.qv.com.cn/tonguebridge/default.aspx
http://www.dailyuniversitybulletin.co.uk/
http://kptz.sinocraftlearn.net/

Template Explanations:
Template 1-
The main information has a dynamic sliding category view that when clicked displays the relevant info.
In addition to the main upper menu it also has a left hand sliding menu that pops out on click or gesture

Template 2-
Has limited number of Articles most of the menus are drop downs from the top menu

Template 3-
No Top menu

Target Market(s)

Teachers, principals and parents

Industry/Entity Type

Education

Requirements
Should not have
• kindergarten preschool feel

```html
<!DOCTYPE html>
<html lang="en">
<head>
<meta charset="utf-8">
<title>Lumra Learning — Home</title>
<link href="https://fonts.googleapis.com/css2?family=PT+Sans:wght@400;700&family=Roboto+Condensed:wght@700&display=swap" rel="stylesheet">
<style>
:root{
  --backdrop:#e3e5e9;
  --page:#ffffff;
  --ink:#444;
  --muted:#8a8a8a;
  --link-blue:#1f5d93;
  --navy:#1c4a7a;
  --blue-top:#2f6aa3;
  --blue-bottom:#184b7e;
  --red-top:#ec4a47;
  --red-bottom:#c81f22;
  --red-link:#d52a2a;
  --line:#e4e4e4;
  --panel-head:#f1f1f1;
  --band-top:#e3edf6;
  --band-bottom:#c7d9ea;
  --orange:#f9ad33;
  --nav-home:#7b1fd0;
  --nav-about:#d8171c;
  --nav-services:#f65a12;
  --nav-blog:#fb9a2a;
  --nav-news:#fbd10d;
  --nav-career:#8ac22a;
  --nav-articles:#2cc9dc;
  --nav-support:#0f2c78;
  --nav-contact:#f21c7d;
}
*{box-sizing:border-box;margin:0;padding:0}
html,body{width:918px;height:1200px;overflow:hidden}
body{background:var(--backdrop);font-family:"PT Sans",sans-serif;color:var(--ink);position:relative}
ul{list-style:none}
.page{position:absolute;left:77px;top:0;width:761px;height:1200px;background:var(--page)}
.abs{position:absolute}

/* header */
.brand{left:106px;top:22px;width:150px;text-align:center}
.brand-dot{display:block;width:34px;height:34px;border-radius:50%;background:var(--red-bottom);margin:0 auto 8px}
.brand-name{font-weight:700;font-size:15px;color:var(--navy);text-transform:uppercase;letter-spacing:.2px}
.search{left:629px;top:74px;width:192px;height:24px;border:1px solid #d3d3d3;border-radius:3px;font-size:9px;font-style:italic;color:#888;padding:6px 10px}
.search svg{position:absolute;right:6px;top:4px}

/* nav */
.main-nav{left:90px;top:112px;width:737px;height:40px;display:flex;border-radius:3px;overflow:hidden}
.main-nav a{display:flex;align-items:center;justify-content:center;color:#fff;text-decoration:none;font-family:"Roboto Condensed",sans-serif;font-weight:700;font-size:12.5px;text-transform:uppercase}
.nav-home{width:74px;background:var(--nav-home)}
.nav-about{width:86px;background:var(--nav-about)}
.nav-services{width:87px;background:var(--nav-services)}
.nav-blog{width:92px;background:var(--nav-blog)}
.nav-news{width:69px;background:var(--nav-news)}
.nav-career{width:77px;background:var(--nav-career)}
.nav-articles{width:84px;background:var(--nav-articles)}
.nav-support{width:83px;background:var(--nav-support)}
.nav-contact{width:85px;background:var(--nav-contact)}

/* hero */
.hero{left:90px;top:159px;width:737px;height:236px;border-radius:4px;background:linear-gradient(180deg,#c9c1b2 0%,#b9a48e 40%,#a5b67c 70%,#d8b5c8 100%)}
.hero-dots{left:437px;top:380px;display:flex;gap:3px}
.hero-dots span{width:9px;height:9px;border-radius:50%;background:#fff}

/* panels */
.panel{border:1px solid var(--line);background:#fff}
.head-red{background:linear-gradient(var(--red-top),var(--red-bottom));color:#fff}
.head-blue{background:linear-gradient(var(--blue-top),var(--blue-bottom));color:#fff}
.head-grey{background:var(--panel-head);color:#333}
.panel-head{height:34px;font-size:15.5px;padding:6px 0 0 20px}

/* select menu */
.select-menu{left:87px;top:408px;width:164px;height:368px}
.select-menu ul{padding:3px 0 0 0}
.select-menu li{height:23.2px;line-height:23px;font-size:10px;color:#555;padding-left:30px;border-bottom:1px solid #ececec;position:relative;margin:0 0 0 0}
.select-menu li:last-child{border-bottom:none}
.select-menu li::before{content:"";position:absolute;left:20px;top:8px;border-left:4px solid #b0b0b0;border-top:3px solid transparent;border-bottom:3px solid transparent}

/* get connected */
.connect{left:87px;top:785px;width:164px;height:166px}
.connect .panel-head{height:31px;padding:6px 0 0 16px}
.connect h3{font-size:11px;font-weight:400;color:#333;margin:11px 0 0 15px}
.connect p{font-size:9px;line-height:14px;color:var(--muted);margin:4px 12px 0 15px}
.social{display:flex;gap:3px;margin:8px 0 0 15px}
.social span{width:22px;height:22px;border-radius:3px;background:linear-gradient(#56a8ea,#1f6ec4)}

/* categories */
.categories{left:261px;top:409px;width:375px;height:257px}
.categories .panel-head{height:34px;padding-top:8px}
.cat-links{display:flex;padding:13px 0 0 25px}
.cat-links ul{width:123px}
.cat-links ul:nth-child(2){width:110px}
.cat-links li{font-size:10px;color:var(--link-blue);height:21.6px;padding-left:9px;position:relative}
.cat-links li::before{content:"";position:absolute;left:0;top:3px;border-left:3.5px solid var(--navy);border-top:3px solid transparent;border-bottom:3px solid transparent}
.cat-band{position:absolute;left:-1px;top:171px;width:375px}
.cat-band div{display:flex;height:28px;align-items:center;background:linear-gradient(var(--band-top),var(--band-bottom));border-bottom:1px solid #fff;font-size:11.5px;color:var(--navy);text-transform:uppercase}
.cat-band span:nth-child(1){width:130px;padding-left:24px}
.cat-band span:nth-child(2){width:130px}

/* latest articles */
.articles{left:261px;top:675px;width:375px;height:276px}
.articles .panel-head{height:35px;padding-top:9px;font-size:15px}
.feature{position:absolute;top:47px;width:164px}
.feature-img{height:76px;border:3px solid #fff;box-shadow:0 0 2px #bbb;background:linear-gradient(135deg,#9c8f83,#d9d4cb 50%,#4d6a7f)}
.feature h4{font-weight:400;font-size:11px;color:#333;margin:10px 0 0 1px}
.feature p{font-size:8.6px;line-height:13.6px;color:var(--muted);margin:4px 0 0 1px}
.thumbs{position:absolute;top:198px;left:15px;display:flex;gap:13px}
.thumbs span{width:76px;height:57px;border:3px solid #fff;box-shadow:0 0 2px #bbb}
.thumbs span:nth-child(1){background:linear-gradient(135deg,#d9cfc4,#f0ede8)}
.thumbs span:nth-child(2){background:linear-gradient(135deg,#4d8f9a,#c5a87d)}
.thumbs span:nth-child(3){background:linear-gradient(135deg,#3b3732,#a8866a)}
.thumbs span:nth-child(4){background:linear-gradient(135deg,#b9c6d3,#7e9bb7)}

/* latest news */
.news{left:644px;top:409px;width:183px;height:302px}
.news .panel-head{height:36px;padding:9px 0 0 17px;font-size:15.5px}
.news article{margin:12px 12px 0 17px}
.news h4{font-weight:400;font-size:10.5px;color:var(--link-blue)}
.news p{font-size:8.4px;line-height:13.6px;color:var(--muted);margin-top:3px}
.news article:nth-child(n+3){margin-top:14px}

/* most popular */
.popular{left:644px;top:722px;width:183px;height:228px}
.popular .panel-head{padding:8px 0 0 19px}
.popular ul{padding:7px 12px 0 21px}
.popular li{height:23.2px;line-height:23px;font-size:9.7px;color:var(--red-link);border-bottom:1px solid #ececec;padding-left:10px;position:relative}
.popular li:last-child{border-bottom:none}
.popular li::before{content:"";position:absolute;left:1px;top:8px;border-left:4px solid var(--red-link);border-top:3.5px solid transparent;border-bottom:3.5px solid transparent}

/* footer */
.footer{left:87px;top:968px;width:740px;height:182px;border-radius:4px 4px 0 0;background:linear-gradient(#3d75ad,#1c5187 60%,#174a80)}
.footer-col{position:absolute;top:26px;padding-right:20px;border-right:1px solid rgba(255,255,255,.12);height:110px}
.footer-col:last-child{border-right:none}
.footer-col h5{font-weight:400;font-size:14px;color:#fff;margin-bottom:7px}
.footer-col li{font-size:9px;color:#e4ecf5;height:17.3px}
.copyright{left:87px;top:1149px;width:740px;height:34px;background:var(--orange);border-radius:0 0 4px 4px;font-size:9px;color:#6b4a12;padding:11px 0 0 37px}
</style>
</head>
<body>
<div class="page"></div>

<header>
  <div class="abs brand"><span class="brand-dot"></span><span class="brand-name">Lumra Learning</span></div>
  <div class="abs search">Search here..
    <svg width="14" height="14" viewBox="0 0 14 14"><circle cx="6" cy="6" r="4.5" fill="none" stroke="#999" stroke-width="1.4"/><line x1="9.3" y1="9.3" x2="12.5" y2="12.5" stroke="#999" stroke-width="1.6"/></svg>
  </div>
  <nav class="abs main-nav">
    <a class="nav-home">Home</a><a class="nav-about">About Us</a><a class="nav-services">Services</a><a class="nav-blog">Blog Post</a><a class="nav-news">News</a><a class="nav-career">Career</a><a class="nav-articles">Articles</a><a class="nav-support">Support</a><a class="nav-contact">Contact</a>
  </nav>
</header>

<div class="abs hero" role="img" aria-label="Photo of four smiling students holding notebooks in front of a campus building"></div>
<div class="abs hero-dots"><span></span><span></span><span></span><span></span></div>

<aside class="abs panel select-menu">
  <div class="panel-head head-red">Select Menu</div>
  <ul>
    <li>Maecenas aliquet</li><li>Mauris malesuada</li><li>Ultricies amet</li><li>Porttitor mattis enim</li><li>Libero interdum</li><li>Blandit sed</li><li>Tempor cursus</li><li>Maecenas aliquet</li><li>Mauris malesuada</li><li>Ultricies amet</li><li>Porttitor mattis enim</li><li>Libero interdum</li><li>Blandit sed</li><li>Tempor cursus</li>
  </ul>
</aside>

<aside class="abs panel connect">
  <div class="panel-head head-blue">Get Connected</div>
  <h3>Get in touch with us</h3>
  <p>Sociosqu ad litora torquent per conubia nostra, per inceptos</p>
  <div class="social"><span></span><span></span><span></span><span></span></div>
</aside>

<section class="abs panel categories">
  <div class="panel-head head-blue">Categories</div>
  <div class="cat-links">
    <ul><li>Maecenas aliquet</li><li>Mauris malesuada</li><li>Ultricies amet</li><li>Porttitor mattis enim</li><li>Libero interdum</li></ul>
    <ul><li>Blandit sed</li><li>Tempor cursus</li><li>Maecenas aliquet</li><li>Mauris malesuada</li><li>Ultricies amet</li></ul>
    <ul><li>Porttitor mattis enim</li><li>Libero interdum</li><li>Blandit sed</li><li>Tempor cursus</li></ul>
  </div>
  <div class="cat-band">
    <div><span>Europe</span><span>Drama</span><span>Math</span></div>
    <div><span>Asia</span><span>Science</span><span>Business Studies</span></div>
    <div><span>USA</span><span>English</span><span>E Commerce</span></div>
  </div>
</section>

<section class="abs panel articles">
  <div class="panel-head head-grey">Latest Articles</div>
  <article class="feature" style="left:15px">
    <div class="feature-img" role="img" aria-label="Photo of students walking down a school staircase"></div>
    <h4>Class aptent taciti</h4>
    <p>Sociosqu ad litora torquent per conubia nostra, per inceptos hymenaeos. Proin nulla arcu, nonummy luctus</p>
  </article>
  <article class="feature" style="left:189px">
    <div class="feature-img" role="img" aria-label="Photo of a teacher with students in a computer lab"></div>
    <h4>Curabitur metus ipsum</h4>
    <p>Sociosqu ad litora torquent per conubia nostra, per inceptos hymenaeos. Proin nulla arcu, nonummy luctus</p>
  </article>
  <div class="thumbs">
    <span role="img" aria-label="Photo of two people at a laptop"></span>
    <span role="img" aria-label="Photo of a globe and books on a desk"></span>
    <span role="img" aria-label="Photo of a student reading"></span>
    <span role="img" aria-label="Photo of students in a classroom"></span>
  </div>
</section>

<aside class="abs panel news">
  <div class="panel-head head-grey">Latest News</div>
  <article><h4>Duis tincidunt lectus</h4><p>Suspendisse vulputate aliquam dui. Nulla elementum dui ut augue.</p></article>
  <article><h4>Scelerisque mi tortor at ipsum</h4><p>Ut ac mi quis lacus mollis aliquam. Curabitur iaculis tempus</p></article>
  <article><h4>Phasellus felis dolor</h4><p>Ut ac mi quis lacus mollis aliquam. Curabitur iaculis tempus eros.</p></article>
  <article><h4>Duis tincidunt lectus</h4><p>Class aptent taciti sociosqu ad litora torquent per conubia nostra, per inceptos hymenaeos.</p></article>
</aside>

<aside class="abs panel popular">
  <div class="panel-head head-red">Most Popular</div>
  <ul>
    <li>Maecenas aliquet velit vel</li><li>Mauris neque malesuada</li><li>Nec ultricies sit amet</li><li>Porttitor mattis enim</li><li>In massa libero interdum</li><li>Blandit sed nulla</li><li>Est eget tempor cursus</li>
  </ul>
</aside>

<footer>
  <div class="abs footer">
    <div class="footer-col" style="left:41px;width:105px"><h5>About Us</h5><ul><li>Overview</li><li>About Us</li><li>What We Do</li><li>How we teach</li><li>Blog Post</li></ul></div>
    <div class="footer-col" style="left:155px;width:136px"><h5>Services Provide</h5><ul><li>Mauris neque metus</li><li>Malesuada nec</li><li>Ultricies sit amet</li><li>Porttitor mattis</li><li>Massa libero</li></ul></div>
    <div class="footer-col" style="left:299px;width:124px"><h5>Sublinks</h5><ul><li>Mauris neque metus</li><li>Malesuada nec</li><li>Ultricies sit amet</li><li>Porttitor mattis</li><li>Massa libero</li></ul></div>
    <div class="footer-col" style="left:432px;width:123px"><h5>Sublinks</h5><ul><li>Mauris neque metus</li><li>Malesuada nec</li><li>Ultricies sit amet</li><li>Porttitor mattis</li><li>Massa libero</li></ul></div>
    <div class="footer-col" style="left:562px;width:130px"><h5>Sublinks</h5><ul><li>Mauris neque metus</li><li>Malesuada nec</li><li>Ultricies sit amet</li><li>Porttitor mattis</li><li>Massa libero</li></ul></div>
  </div>
  <div class="abs copyright">Copyright © 2013 Company Name.&nbsp; All right reserved.</div>
</footer>
</body>
</html>
```